Business Card Design

Buy and sell properties
Buy and rehab properties
Buy properties for cash
That is what I do but do need a logo
looking for some type of logo or design on it
Just started business
Back of card should say something like BUY HOUSES CASH
Overview: it is a new company. Basically I buy properties wholesale and fix them up and sell them or sell them to other fix and flippers
Background: company is new so not any background
Market: is basically anyone selling a house or buying a house. Someone that needs to sell house fast. Basically I am a cash home buyer!!!

Updates
Email on card should be:   harborlanerealtyinc@mailnest.com

Industry/Entity Type
House
Contact Information for Business Card
Harbor Lane Realty Inc
PO Box 718296
Coral Mill Key FL 33071

Dwight Kallum
dkallum@mailnest.com
305-271-5589

```html
<!DOCTYPE html>
<html lang="en">
<head>
<meta charset="utf-8">
<title>Harbor Lane Realty Inc — Business Card</title>
<link rel="stylesheet" href="https://fonts.googleapis.com/css2?family=Open+Sans:ital,wght@0,400;1,400;1,700&family=Ubuntu:wght@400;500&display=swap">
<style>
  :root {
    --canvas: #e4e5e7;
    --blue: #1e7fc1;
    --blue-deep: #176fae;
    --blue-light: #2a8fd0;
    --paper: #f4f5f6;
    --white: #ffffff;
    --ink-blue: #1d6fb0;
  }
  * { box-sizing: border-box; margin: 0; padding: 0; }
  html, body { width: 1200px; height: 1000px; overflow: hidden; }
  body {
    background: var(--canvas);
    position: relative;
    font-family: "Open Sans", sans-serif;
  }
  .card {
    position: absolute;
    left: 250px;
    width: 700px;
    height: 400px;
    overflow: hidden;
    box-shadow: 0 6px 18px rgba(0,0,0,0.18);
  }
  .card--front { top: 70px; background: linear-gradient(135deg, var(--blue-deep), var(--blue-light)); }
  .card--back { top: 530px; background: var(--paper); }

  /* Brand name block */
  .brand {
    position: absolute;
    display: flex;
    align-items: center;
    gap: 18px;
    color: var(--white);
    font-family: "Ubuntu", sans-serif;
    font-weight: 400;
  }
  .brand__mark { width: 22px; height: 22px; background: var(--white); flex: none; }
  .brand__name { line-height: 1; }
  .brand__line1 { display: block; letter-spacing: 1px; }
  .brand__line2 { display: block; text-align: right; letter-spacing: 0.5px; margin-top: 6px; }

  .card--front .brand { left: 150px; top: 120px; }
  .card--front .brand__line1 { font-size: 56px; }
  .card--front .brand__line2 { font-size: 22px; }

  .front__email {
    position: absolute;
    left: 0; right: 0;
    top: 290px;
    text-align: center;
    color: var(--white);
    font-family: "Ubuntu", sans-serif;
    font-weight: 500;
    font-size: 20px;
    letter-spacing: 3px;
  }

  /* Back */
  .back__panel {
    position: absolute;
    left: 324px; top: 0;
    width: 376px; height: 400px;
    background: linear-gradient(135deg, var(--blue-deep), var(--blue-light));
  }
  .card--back .brand { left: 30px; top: 95px; gap: 14px; }
  .card--back .brand__line1 { font-size: 40px; }
  .card--back .brand__line2 { font-size: 16px; }
  .back__tagline {
    position: absolute;
    left: 0; right: 0; bottom: 48px;
    text-align: center;
    color: var(--white);
    font-family: "Ubuntu", sans-serif;
    font-size: 24px;
    letter-spacing: 6px;
  }
  .band {
    position: absolute;
    left: 0;
    width: 324px;
    height: 38px;
    background: var(--blue);
    color: var(--white);
    font-style: italic;
    display: flex;
    align-items: center;
    justify-content: center;
  }
  .band--name { top: 46px; font-weight: 700; font-size: 22px; }
  .band--phone { top: 96px; font-size: 18px; }
  .band--email { top: 146px; font-size: 18px; }

  .company {
    position: absolute;
    left: 28px; top: 236px;
    color: var(--ink-blue);
    font-size: 15px;
    line-height: 1.55;
  }
  .company__name { font-size: 18px; margin-bottom: 4px; }
</style>
</head>
<body>
  <section class="card card--front" aria-label="Card front">
    <div class="brand">
      <span class="brand__mark"></span>
      <span class="brand__name">
        <span class="brand__line1">HARBOR LANE</span>
        <span class="brand__line2">REALTY INC</span>
      </span>
    </div>
    <p class="front__email">harborlanerealtyinc@mailnest.com</p>
  </section>

  <section class="card card--back" aria-label="Card back">
    <div class="band band--name">Dwight Kallum</div>
    <div class="band band--phone">Phone : 305-271-5589</div>
    <div class="band band--email">Email : dkallum@mailnest.com</div>

    <div class="company">
      <p class="company__name">Harbor Lane Realty Inc</p>
      <p>PO Box 718296</p>
      <p>Coral Mill Key FL 33071</p>
      <p>Email : harborlanerealtyinc@mailnest.com</p>
    </div>

    <div class="back__panel">
      <div class="brand">
        <span class="brand__mark"></span>
        <span class="brand__name">
          <span class="brand__line1">HARBOR LANE</span>
          <span class="brand__line2">REALTY INC</span>
        </span>
      </div>
      <p class="back__tagline">BUY HOUSES CASH</p>
    </div>
  </section>
</body>
</html>
```